Printer Cartridges Supplier Namecard

Attached is my company logo and the design of my current namecard. I would like to have a more special look for it. Can have a little cuteness too rather than those normal standard feel. I'm a supplier mainly dealing with original and compatible printer toner cartridges, some other products like paper supplies as well.

Target Market(s)

Companies, businesses, corporates

Industry/Entity Type

It Company

Contact Information for Business Card

Logo, name, contact, address, supplies and maybe a slogan

Colors
85cae6
33a6d7
3176b5
0255a3
0792cd
85abd2

Requirements
Must have
• Logo, name, contact and address basic details.
• Must include some pictures, not just rearrange what I'm currently having.
Nice to have
• Be creative and bold, a diiferent traditional feel.

```html
<!DOCTYPE html>
<html lang="en">
<head>
<meta charset="utf-8">
<title>tonerbay.sg business card</title>
<link rel="stylesheet" href="https://fonts.googleapis.com/css2?family=Lato:wght@400;700&display=swap">
<style>
  :root {
    --sky: #5db8e6;
    --sky-deep: #33a6d7;
    --slate: #5f7284;
    --ink: #4a4d52;
    --rule: #8a8d91;
    --paper: #ffffff;
    --stage: #eceef0;
    --muted: #5b5e63;
  }
  * { margin: 0; padding: 0; box-sizing: border-box; }
  html, body { width: 1200px; height: 900px; overflow: hidden; }
  body {
    background: var(--stage);
    font-family: "Lato", sans-serif;
    position: relative;
  }
  .card {
    position: absolute;
    left: 300px;
    width: 600px;
    height: 343px;
    border-radius: 3px;
    overflow: hidden;
    box-shadow: 0 6px 18px rgba(0,0,0,0.12);
  }
  /* Front */
  .card-front {
    top: 80px;
    background: radial-gradient(ellipse at 85% 0%, var(--sky) 0%, var(--sky) 30%, #4f95bd 65%, var(--slate) 100%);
    color: var(--paper);
  }
  .brand {
    position: absolute;
    display: flex;
    align-items: center;
    gap: 14px;
    font-weight: 700;
  }
  .brand-mark { display: block; border-radius: 6px; }
  .card-front .brand { left: 150px; top: 82px; font-size: 60px; letter-spacing: 1px; }
  .card-front .brand-mark { width: 62px; height: 62px; background: var(--paper); }
  .tagline {
    position: absolute;
    left: 228px; top: 152px;
    font-size: 12px;
    letter-spacing: 0.3px;
  }
  .services {
    position: absolute;
    left: 60px; top: 218px;
    display: grid;
    grid-template-columns: 265px 240px;
    row-gap: 6px;
    list-style: none;
    font-size: 17px;
  }
  .services li::before {
    content: "";
    display: inline-block;
    width: 8px; height: 8px;
    border-radius: 50%;
    background: var(--paper);
    margin-right: 9px;
    vertical-align: middle;
  }
  /* Back */
  .card-back { top: 470px; background: var(--paper); color: var(--ink); }
  .card-back .brand { right: 40px; top: 34px; font-size: 54px; color: var(--ink); }
  .card-back .brand-mark { width: 56px; height: 56px; background: var(--sky); }
  .logo-rule {
    position: absolute; left: 250px; right: 30px; top: 118px;
    height: 1px; background: var(--rule);
  }
  .person { position: absolute; left: 36px; top: 146px; }
  .person-name { font-size: 30px; color: var(--sky); font-weight: 400; }
  .person-role { font-size: 17px; color: var(--ink); margin-top: 1px; }
  .name-rule {
    position: absolute; left: 196px; right: 30px; top: 186px;
    height: 1px; background: var(--rule);
  }
  .contacts { position: absolute; left: 36px; top: 232px; list-style: none; font-size: 17px; }
  .contacts li { display: flex; align-items: center; gap: 10px; height: 25px; }
  .contacts svg { width: 14px; height: 14px; fill: var(--sky); }
  .address {
    position: absolute; right: 30px; top: 200px;
    font-style: normal; font-size: 14px; line-height: 1.35; text-align: right;
    color: var(--muted);
  }
  .band-blue { position: absolute; left: 300px; right: 130px; bottom: 22px; height: 10px; background: var(--sky); }
  .band-slate { position: absolute; right: 0; width: 130px; bottom: 22px; height: 72px; background: var(--muted); }
  .band-base { position: absolute; left: 0; right: 0; bottom: 0; height: 10px; background: var(--sky); }
</style>
</head>
<body>
  <section class="card card-front">
    <div class="brand"><span class="brand-mark"></span>tonerbay.sg</div>
    <p class="tagline">Compatible printer ink and toner solutions</p>
    <ul class="services">
      <li>Printer Ink &amp; Toner Cartridges</li>
      <li>Paper Products</li>
      <li>Original Printer Cartridges</li>
      <li>Printer Maintainence &amp; Repair</li>
    </ul>
  </section>

  <section class="card card-back">
    <div class="brand"><span class="brand-mark"></span>tonerbay.sg</div>
    <div class="logo-rule"></div>
    <div class="person">
      <h1 class="person-name">Mira Tan</h1>
      <p class="person-role">Sales Executive</p>
    </div>
    <div class="name-rule"></div>
    <ul class="contacts">
      <li><svg viewBox="0 0 14 14"><rect x="3" y="0" width="8" height="14" rx="1.5"/><rect x="4.5" y="2" width="5" height="8" fill="#fff"/></svg>9000 1234</li>
      <li><svg viewBox="0 0 14 14"><rect x="0" y="2" width="14" height="10" rx="1"/><path d="M1 3 L7 8 L13 3" stroke="#fff" stroke-width="1.2" fill="none"/></svg>mira@tonerbay.sg</li>
      <li><svg viewBox="0 0 14 14"><circle cx="7" cy="7" r="7"/><path d="M1 7 H13 M7 1 C4 4 4 10 7 13 M7 1 C10 4 10 10 7 13" stroke="#fff" stroke-width="1" fill="none"/></svg>www.tonerbay.sg</li>
    </ul>
    <address class="address">14A Harbourline Crescent<br>#05-118, Singapore 510214</address>
    <div class="band-blue"></div>
    <div class="band-slate"></div>
    <div class="band-base"></div>
  </section>
</body>
</html>
```